Young, dynamic furniture company needs a new business card design

We require a new business card design for our modern furniture company which supplies furniture and appliances to the property and development market.
Oakridge Interiors has become one of the leading furniture & appliance suppliers to the property market withing London. With over 10 years experience, we have increased our business to supply not only private landlords and managing agents, but also property developers, housing associations and local councils.
We offer not only a complete range of furniture which includes beds, wardrobes, dining sets and sofas, but also a high quality, full delivery and assembly service to help you with all our furnishing needs.

Target Market(s)

Private landlords, estate agents, letting agents, property management companies

Industry/Entity Type

Business

Contact Information for Business Card

Name,
Title,
Address,
Mobile,
Telephone,
Fax, Website, email address

Font styles to use
Sans Serif

Colors
3176b5
0555a3
85abd2
cfdeed

Requirements
Must have
• All the above information for each of our staff, along with our logo

```html
<!DOCTYPE html>
<html lang="en">
<head>
<meta charset="utf-8">
<title>Oakridge Interiors – Business Card</title>
<link rel="stylesheet" href="https://fonts.googleapis.com/css2?family=Montserrat:wght@400;500;600;700&display=swap">
<style>
  :root {
    --brand-navy: #1d4b9e;
    --brand-deep: #0555a3;
    --brand-mid: #3176b5;
    --brand-sky: #2a9fd8;
    --brand-soft: #85abd2;
    --brand-pale: #cfdeed;
    --ink: #2a2a2e;
    --card-white: #f7f7f7;
    --stage: #e4e7ec;
  }
  * { box-sizing: border-box; margin: 0; padding: 0; }
  html, body { width: 1200px; height: 780px; overflow: hidden; }
  body {
    background: var(--stage);
    font-family: "Montserrat", sans-serif;
    position: relative;
  }
  .card {
    position: absolute;
    top: 125px;
    width: 340px;
    height: 530px;
    border-radius: 18px;
    overflow: hidden;
    box-shadow: 0 10px 28px rgba(20, 30, 60, 0.18);
  }

  /* Front */
  .card-front { left: 215px; background: var(--card-white); }
  .brand-block { position: absolute; top: 58px; left: 0; right: 0; text-align: center; }
  .brand-mark {
    display: inline-block; width: 34px; height: 34px;
    background: var(--brand-navy); margin-bottom: 16px;
  }
  .brand-name {
    font-size: 25px; font-weight: 500; letter-spacing: 1.5px;
    color: var(--ink); text-transform: uppercase; line-height: 1.1;
  }
  .brand-tagline {
    margin-top: 6px; font-size: 11px; font-weight: 400; letter-spacing: 1.4px;
    color: var(--ink); text-transform: uppercase;
  }
  .staff { position: absolute; top: 208px; left: 34px; right: 24px; }
  .staff-name {
    font-size: 21px; font-weight: 700; letter-spacing: 1px; text-transform: uppercase;
    color: var(--brand-navy);
  }
  .staff-name .surname { color: var(--brand-sky); }
  .staff-title { font-size: 14px; font-weight: 500; color: var(--ink); margin-top: 2px; letter-spacing: .3px; }
  .address { margin-top: 22px; font-size: 13.5px; line-height: 1.45; color: var(--ink); letter-spacing: .4px; }
  .contacts { margin-top: 16px; list-style: none; font-size: 13.5px; line-height: 1.5; color: var(--ink); letter-spacing: .6px; }
  .contacts .label { color: var(--brand-navy); font-weight: 600; display: inline-block; width: 26px; }
  .footer-rule {
    position: absolute; left: 0; right: 0; bottom: 86px; height: 3px; background: var(--brand-sky);
  }
  .footer-band {
    position: absolute; left: 0; right: 0; bottom: 0; height: 80px;
    background: var(--brand-navy);
    display: flex; align-items: center; justify-content: center;
  }
  .website { color: #ffffff; font-size: 15px; font-weight: 600; letter-spacing: 1.2px; }

  /* Back */
  .card-back {
    left: 645px;
    background: linear-gradient(160deg, #2456aa 0%, var(--brand-navy) 50%, #173e88 100%);
  }
  .back-decoration {
    position: absolute; inset: 0;
    background: linear-gradient(135deg, rgba(255,255,255,0.06) 0%, rgba(255,255,255,0) 60%);
  }
  .back-lockup {
    position: absolute; top: 50%; left: 50%;
    width: 460px;
    transform: translate(-50%, -50%) rotate(90deg);
    text-align: center; color: #ffffff;
  }
  .back-name { font-size: 36px; font-weight: 500; letter-spacing: 2px; text-transform: uppercase; line-height: 1.1; }
  .back-tagline { margin-top: 8px; font-size: 17px; font-weight: 400; letter-spacing: 2px; text-transform: uppercase; }
</style>
</head>
<body>
  <article class="card card-front">
    <div class="brand-block">
      <span class="brand-mark"></span>
      <p class="brand-name">Oakridge Interiors</p>
      <p class="brand-tagline">Trade Furniture Solutions</p>
    </div>
    <div class="staff">
      <h1 class="staff-name">Marcus <span class="surname">Ellery</span></h1>
      <p class="staff-title">Managing Director</p>
      <p class="address">Trade Showroom &amp; Office<br>22B Halden Trade Estate<br>Westbury Road London, N14 6QR</p>
      <ul class="contacts">
        <li><span class="label">T :</span>020 7946 0321</li>
        <li><span class="label">F :</span>020 7946 0322</li>
        <li><span class="label">M :</span>07700 90 41 57</li>
        <li><span class="label">E :</span>marcus@oakridgeint.co.uk</li>
      </ul>
    </div>
    <div class="footer-rule"></div>
    <div class="footer-band"><span class="website">www.oakridgeint.co.uk</span></div>
  </article>

  <article class="card card-back">
    <div class="back-decoration" role="img" aria-label="Faint large brand symbol in deep blue tones"></div>
    <div class="back-lockup">
      <p class="back-name">Oakridge Interiors</p>
      <p class="back-tagline">Trade Furniture Solutions</p>
    </div>
  </article>
</body>
</html>
```